Banner ads for LP that work with same theme as below banners

Love the banner ads below. Need more with attached photos. But use the same wording, font as in below banner ads. Should be LP size 1200/627 so I can use for Pixorly and LP. Looking for great ads to use as LP ads. We do lots of ads so it will be worth your time to enter this contest you will be rewarded with a ton of work. Need several banner ads that work together. So maybe 1 of the dresses, 1 of the sweater, 1 of the leggings, 1 of the jacket

Target Market(s)

Women 24-45

Industry/Entity Type

Fashion

Requirements
Must have
• Banner ads that work for LP and Pixorly
Nice to have
• Several options to choose from
Should not have
• not sure

```html
<!DOCTYPE html>
<html lang="en">
<head>
<meta charset="utf-8">
<title>Our Best Dresses Ever – Banner</title>
<link rel="stylesheet" href="https://fonts.googleapis.com/css2?family=Kaushan+Script&family=Tinos:wght@400;700&display=swap">
<style>
  :root {
    --charcoal: #2f2f2f;
    --charcoal-light: #474747;
    --sand: #d8d5bd;
    --sand-dark: #a9a790;
    --paper: #ffffff;
    --ink: #000000;
    --photo-dark: #1c1a1a;
    --photo-warm: #8a6a4e;
  }
  * { margin: 0; padding: 0; box-sizing: border-box; }
  html, body { width: 1200px; height: 627px; overflow: hidden; background: var(--paper); }
  .banner { position: relative; width: 1200px; height: 627px; overflow: hidden; }
  .backdrop { position: absolute; inset: 0; }
  .headline {
    position: absolute; left: 150px; top: 70px; width: 380px;
    color: var(--paper); text-align: center;
  }
  .headline .script {
    display: block; font-family: "Kaushan Script", cursive;
    font-size: 62px; line-height: 1.1;
  }
  .headline .category {
    display: block; font-family: "Tinos", serif; font-weight: 700;
    font-size: 52px; letter-spacing: 18px; line-height: 1.35;
    margin: 4px 0 6px 18px;
  }
  .model-photo {
    position: absolute; left: 700px; top: 0; width: 410px; height: 610px;
    background: linear-gradient(180deg, var(--photo-warm) 0%, var(--photo-dark) 42%, var(--photo-dark) 100%);
  }
  .cta {
    position: absolute; left: 125px; top: 452px; width: 410px; height: 146px;
    border-radius: 50%; background: var(--ink);
    border: 6px solid var(--paper); box-shadow: 0 0 0 2px var(--ink);
    display: flex; align-items: center; justify-content: center;
    font-family: "Tinos", serif; font-size: 38px; color: var(--paper);
    text-decoration: none;
  }
  .cta strong { font-weight: 700; }
  .cta span { margin: 0 10px; }
</style>
</head>
<body>
<main class="banner">
  <svg class="backdrop" width="1200" height="627" viewBox="0 0 1200 627" role="img" aria-label="Low-poly geometric background in charcoal and sand tones">
    <defs>
      <linearGradient id="sandTone" x1="0" y1="0" x2="1" y2="1">
        <stop offset="0" stop-color="var(--sand)"/>
        <stop offset="1" stop-color="var(--sand-dark)"/>
      </linearGradient>
      <linearGradient id="charcoalTone" x1="0" y1="0" x2="1" y2="1">
        <stop offset="0" stop-color="var(--charcoal-light)"/>
        <stop offset="1" stop-color="var(--charcoal)"/>
      </linearGradient>
    </defs>
    <rect class="sand-field" width="1200" height="627" fill="url(#sandTone)"/>
    <polygon class="charcoal-field" points="0,12 1150,12 330,500 0,627" fill="url(#charcoalTone)"/>
    <polygon class="paper-strip" points="0,615 540,552 1200,600 1200,627 0,627" fill="var(--paper)"/>
  </svg>

  <h1 class="headline">
    <span class="script">Our Best</span>
    <span class="category">DRESSES</span>
    <span class="script">Ever!</span>
  </h1>

  <div class="model-photo" role="img" aria-label="Photo of a model with long wavy hair wearing a black lace skater dress"></div>

  <a class="cta" href="#"><strong>SHOP</strong><span>THE</span><strong>LOOK</strong></a>
</main>
</body>
</html>
```